Soho based IT support firm flyer.

We need a flyer to boost our business. We're a tech support firm based in Soho, London and provide helpdesk and call out support to SMEs in and around London.
They'll be two flyers with the same design. One is location specific and has the copy:
-
1 Month Free IT Support!
Based in Soho, we provide expert tech support for both Lumex machines and PCs.
We have monthly as well as pay-as-you-go plans to fit your business.
Call us now and we'll show you how we can save you up to 50% on your IT spend.
-None location based is-
1 Month Free IT Support!
We provide expert, professional tech support for both Lumex machines and PCs.
• Dedicated full time helpdesk
• Same day onsite visits
• Proactive support with monitoring
• 98% satisfaction score*
*taken from satisfaction survey sent out on closure of every case for Oct 2011 to Oct 2012
-
The location one needs to include a map with our location marked as postcode K7R 4TB.
I'm fine with royalty photos being used within a reasonable price. Please use Pixmarrow.
Our site shows our brand best. Please keep as close to this as possible.
http://quillnet-hub.example
Thanks for looking.

```html
<!DOCTYPE html>
<html lang="en">
<head>
<meta charset="utf-8">
<title>Quillnet Hub – IT Support Flyer</title>
<link rel="stylesheet" href="https://fonts.googleapis.com/css2?family=Arimo:ital,wght@0,400;0,700;1,400&display=swap">
<style>
  :root {
    --lime: #b5d334;
    --lime-light: #c6df5a;
    --lime-dark: #94b42a;
    --cream: #f3f3ea;
    --top-strip: #e2e2d4;
    --leaf-dark: #2f5a1a;
    --leaf-mid: #6f9a2e;
    --leaf-light: #c8dc83;
    --card: #ffffff;
    --body-text: #555555;
    --orange: #f7a02c;
    --map-base: #ece6dc;
    --map-road: #f4b94a;
    --footer: #464646;
    --white: #ffffff;
  }
  * { margin: 0; padding: 0; box-sizing: border-box; }
  html, body { width: 851px; height: 1200px; overflow: hidden; }
  body {
    position: relative;
    background: var(--cream);
    font-family: "Arimo", Arial, sans-serif;
    color: var(--body-text);
  }
  .top-strip { position: absolute; left: 0; top: 0; width: 851px; height: 10px; background: var(--top-strip); }
  .masthead {
    position: absolute; left: 0; top: 10px; width: 851px; height: 93px;
    background: var(--white);
    display: flex; align-items: center; justify-content: center;
  }
  .brand-name {
    font-size: 50px; font-weight: 700; color: var(--lime-dark);
    letter-spacing: -0.5px;
    display: flex; align-items: center; gap: 12px;
  }
  .brand-dot { width: 16px; height: 16px; border-radius: 50%; background: var(--lime-dark); }
  .hero-photo {
    position: absolute; left: 0; top: 103px; width: 851px; height: 317px;
    background: linear-gradient(90deg, var(--leaf-mid) 0%, var(--leaf-dark) 12%, var(--leaf-light) 24%, var(--leaf-mid) 36%, var(--leaf-dark) 48%, var(--leaf-light) 62%, var(--leaf-mid) 74%, var(--leaf-dark) 86%, var(--leaf-light) 100%);
  }
  .hero-rule { position: absolute; left: 0; top: 420px; width: 851px; height: 10px; background: var(--lime); }
  .hero-panel {
    position: absolute; left: 175px; top: 143px; width: 483px; height: 158px;
    background: rgba(40, 50, 30, 0.5);
    border-radius: 4px;
    text-align: center; color: var(--white);
    padding-top: 12px;
    text-shadow: 0 1px 2px rgba(0,0,0,0.3);
  }
  .hero-kicker { font-size: 12px; font-weight: 700; letter-spacing: 0.3px; }
  .hero-title { font-size: 38px; font-weight: 700; line-height: 38px; margin-top: 2px; }
  .hero-subtitle { font-size: 36px; font-weight: 400; line-height: 38px; }
  .hero-blurb { font-size: 12px; line-height: 19px; margin-top: 5px; }
  .offer-card {
    position: absolute; left: 132px; top: 338px; width: 574px; height: 712px;
    background: var(--card);
    box-shadow: 0 0 3px rgba(0,0,0,0.15);
  }
  .offer-banner {
    position: absolute; left: 31px; top: 30px; width: 511px; height: 77px;
    background: linear-gradient(var(--lime-light), var(--lime));
    border-radius: 5px;
    box-shadow: 0 2px 3px rgba(0,0,0,0.2);
    color: var(--white);
    font-size: 37px; font-weight: 400; line-height: 77px; text-align: center;
    text-shadow: 0 1px 2px rgba(0,0,0,0.25);
  }
  .offer-banner strong { font-weight: 700; }
  .offer-points {
    position: absolute; left: 33px; top: 142px; width: 505px;
    list-style: none; font-size: 21px; line-height: 31px;
  }
  .offer-points li { margin-bottom: 32px; }
  .location-band {
    position: absolute; left: 2px; top: 462px; width: 567px; height: 247px;
    background: var(--orange);
  }
  .location-map {
    position: absolute; left: 20px; top: 17px; width: 322px; height: 213px;
    background: linear-gradient(160deg, var(--map-base) 0%, #e4ddd0 60%, var(--map-road) 100%);
  }
  .location-map svg { position: absolute; left: 150px; top: 80px; }
  .location-address {
    position: absolute; left: 352px; top: 76px; width: 200px;
    text-align: center; color: var(--white);
  }
  .location-label { font-size: 13px; font-style: italic; }
  .location-lines { font-size: 17px; font-weight: 700; line-height: 20px; }
  .site-footer {
    position: absolute; left: 0; top: 1050px; width: 851px; height: 150px;
    background: var(--footer); color: var(--white); text-align: center;
  }
  .footer-brand {
    margin-top: 18px; font-size: 32px; font-weight: 700; color: var(--white);
    display: inline-flex; align-items: center; gap: 9px;
  }
  .footer-brand .brand-dot { width: 11px; height: 11px; background: var(--white); }
  .footer-rule { width: 420px; height: 1px; margin: 8px auto 0; background: rgba(255,255,255,0.15); }
  .footer-lead { font-size: 17px; font-style: italic; margin-top: 11px; }
  .footer-contacts {
    margin-top: 9px; font-size: 16px;
    display: flex; justify-content: center; gap: 18px; align-items: center;
  }
  .footer-contacts .sep { width: 8px; height: 8px; border-radius: 50%; background: var(--white); }
</style>
</head>
<body>
  <div class="top-strip"></div>
  <header class="masthead">
    <div class="brand-name">Quillnet Hub <span class="brand-dot"></span></div>
  </header>

  <div class="hero-photo" role="img" aria-label="Soft-focus photograph of green grass blades"></div>
  <div class="hero-rule"></div>

  <section class="hero-panel">
    <p class="hero-kicker">WE'RE ABOUT</p>
    <h1 class="hero-title">Friendly &amp; Reliable</h1>
    <p class="hero-subtitle">Tech Support</p>
    <p class="hero-blurb">IT Support, Consultancy and Project Management. A one stop shop<br>for all of your business' IT needs.</p>
  </section>

  <main class="offer-card">
    <h2 class="offer-banner"><strong>1 Month Free</strong> I.T. Support!</h2>
    <ul class="offer-points">
      <li>* Based in Soho, we provide expert tech support for both Lumex machines and PCs.</li>
      <li>* We have monthly as well as pay-as-you-go plans to fit your business.</li>
      <li>* Call us now and we'll show you how we can save you up to 50% on your IT spend.</li>
    </ul>

    <section class="location-band">
      <div class="location-map" role="img" aria-label="Street map of the Soho area with the office location marked">
        <svg width="22" height="30" viewBox="0 0 22 30" aria-hidden="true">
          <path d="M11 1 C5 1 1 5 1 11 C1 18 11 29 11 29 C11 29 21 18 21 11 C21 5 17 1 11 1 Z" fill="#e0463a" stroke="#a82a20"/>
          <circle cx="11" cy="11" r="3.5" fill="#7a1a12"/>
        </svg>
      </div>
      <div class="location-address">
        <p class="location-label">Visit us at:</p>
        <p class="location-lines">12-14 Marlow House,<br>Harrow Lane,<br>London<br>K7R 4TB</p>
      </div>
    </section>
  </main>

  <footer class="site-footer">
    <div class="footer-brand">Quillnet Hub <span class="brand-dot"></span></div>
    <div class="footer-rule"></div>
    <p class="footer-lead">You can also contact us at:</p>
    <p class="footer-contacts">
      <span>Ph.: 0203 555 0147</span><span class="sep"></span>
      <span>Email: info@quillnet-hub.example</span><span class="sep"></span>
      <span>Website: www.quillnet-hub.example</span>
    </p>
  </footer>
</body>
</html>
```